Business Card Design

Tumble Harbor is a Laundromat Store
we provide wash and Fold service to Customers who are busy with their life and can not come to the store and do laundry
we have customers who drop their laundry at the store
but now i want to provide service to customers who are not able to come to the store to drop. i will go to their address and pickup the laundry and get it washed folded and delivered
Updates
Can you use the colour in you design which i uploaded and also fusha fluorescent green bright pink
Target Market(s)
all works of life who don't have time to do laundry
Industry/Entity Type
Store
Contact Information for Business Card
TumbleHarbor Laundromat
247 Mallory Street
Lynn MA 01938
Look and feel
Each slider illustrates characteristics of the customer's brand and the style your logo design should communicate.

```html
<!DOCTYPE html>
<html lang="en">
<head>
<meta charset="utf-8">
<title>TumbleHarbor Laundromat – Business Card</title>
<link href="https://fonts.googleapis.com/css2?family=Lato:wght@400;700;900&display=swap" rel="stylesheet">
<style>
  :root {
    --page-bg: #3a3a3c;
    --plum-deep: #1c0a1d;
    --plum-mid: #3e1640;
    --band-light: #9c2a8e;
    --band-dark: #5a1458;
    --fuchsia: #d42c8e;
    --white: #ffffff;
    --laundry-mixed-a: #c9a3c4;
    --laundry-mixed-b: #6d7fb5;
    --laundry-folded-a: #8ea0c8;
    --laundry-folded-b: #c7496f;
    --arrow: #f2e6f2;
  }
  * { margin: 0; padding: 0; box-sizing: border-box; }
  html, body { width: 1200px; height: 900px; overflow: hidden; }
  body {
    background: var(--page-bg);
    font-family: "Lato", Arial, sans-serif;
    color: var(--white);
    position: relative;
  }
  .business-card {
    position: absolute;
    left: 60px; top: 120px;
    width: 1080px; height: 660px;
    overflow: hidden;
    background: radial-gradient(ellipse at 50% 35%, var(--plum-mid) 0%, var(--plum-deep) 75%);
  }
  .brand {
    position: absolute; top: 38px; width: 100%;
    text-align: center; font-size: 50px; line-height: 1;
  }
  .brand-name { font-weight: 900; }
  .brand-type { font-weight: 400; }
  .address {
    position: absolute; top: 106px; width: 100%;
    text-align: center; font-size: 24px; letter-spacing: 5px; font-weight: 400;
  }
  .call-box {
    position: absolute; top: 152px; left: 50%; transform: translateX(-50%);
    background: var(--fuchsia); padding: 6px 16px;
    font-size: 20px; font-weight: 700; white-space: nowrap;
  }
  .call-box .phone { font-size: 28px; font-weight: 400; margin-left: 6px; }
  .laundry-pile {
    position: absolute; left: 280px; top: 218px; width: 250px; height: 152px;
    border-radius: 46% 50% 18% 22% / 60% 60% 14% 14%;
    background: linear-gradient(160deg, var(--laundry-mixed-a), var(--laundry-mixed-b));
  }
  .laundry-stack {
    position: absolute; left: 610px; top: 206px; width: 180px; height: 164px;
    border-radius: 14px;
    background: linear-gradient(180deg, var(--laundry-folded-a), var(--laundry-folded-b));
  }
  .from-to {
    position: absolute; left: 484px; top: 222px; width: 136px; height: 136px;
    border-radius: 50%; background: var(--fuchsia);
    text-align: center; font-size: 29px; font-weight: 400;
  }
  .from-to .from { position: absolute; top: 24px; left: 0; width: 100%; }
  .from-to .to { position: absolute; top: 78px; left: 0; width: 100%; font-weight: 700; }
  .from-to svg { position: absolute; left: 23px; top: 61px; }
  .band { position: absolute; left: 0; top: 0; }
  .step {
    position: absolute; width: 230px; text-align: center;
    font-size: 20px; font-weight: 700; line-height: 1.2;
  }
  .step-circle {
    width: 108px; height: 108px; margin: 0 auto 20px;
    border-radius: 50%; background: var(--white);
    display: flex; align-items: center; justify-content: center;
  }
  .step-art { width: 76px; height: 68px; border-radius: 10px; }
  .step-art.washer { background: linear-gradient(135deg, #9aa6b8, #5f6f86); }
  .step-art.smile { width: 70px; height: 70px; border-radius: 50%; background: radial-gradient(circle at 40% 35%, #fff27a, #f0b400); }
  .step-1 { left: 40px; top: 448px; }
  .step-2 { left: 318px; top: 430px; }
  .step-3 { left: 596px; top: 410px; }
  .step-4 { left: 850px; top: 388px; font-size: 18px; }
</style>
</head>
<body>
  <section class="business-card" aria-label="TumbleHarbor Laundromat business card">
    <svg class="band" width="1080" height="660" viewBox="0 0 1080 660" aria-hidden="true">
      <defs>
        <linearGradient id="bandFill" x1="0" y1="0" x2="0" y2="1">
          <stop offset="0" stop-color="var(--band-light)"/>
          <stop offset="1" stop-color="var(--band-dark)"/>
        </linearGradient>
      </defs>
      <path d="M0 430 Q540 300 1080 400 L1080 660 L0 660 Z" fill="url(#bandFill)"/>
      <g fill="none" stroke="var(--arrow)" stroke-width="3" stroke-linecap="round" stroke-linejoin="round">
        <path d="M230 500 Q280 480 330 494"/><path d="M318 484 L332 495 L316 503"/>
        <path d="M508 480 Q558 460 608 474"/><path d="M596 464 L610 475 L594 483"/>
        <path d="M786 458 Q836 438 886 452"/><path d="M874 442 L888 453 L872 461"/>
      </g>
    </svg>

    <h1 class="brand"><span class="brand-name">TumbleHarbor</span> <span class="brand-type">LAUNDROMAT</span></h1>
    <p class="address">247 MALLORY STREET LYNN MA 01938</p>
    <p class="call-box">CALL US: <span class="phone">079 555 01234</span></p>

    <div class="laundry-pile" role="img" aria-label="Photo of a heap of unwashed colourful clothes"></div>
    <div class="laundry-stack" role="img" aria-label="Photo of a neat stack of folded clean clothes"></div>

    <div class="from-to">
      <span class="from">FROM</span>
      <svg width="90" height="16" viewBox="0 0 90 16" aria-hidden="true">
        <path d="M4 8 H86 M12 2 L4 8 L12 14" fill="none" stroke="#fff" stroke-width="2" stroke-dasharray="4 3"/>
      </svg>
      <span class="to">TO</span>
    </div>

    <div class="step step-1">
      <div class="step-circle">
        <svg width="74" height="70" viewBox="0 0 74 70" aria-hidden="true">
          <rect x="4" y="10" width="66" height="56" rx="4" fill="#fff" stroke="#222" stroke-width="4"/>
          <rect x="4" y="10" width="66" height="16" fill="#c62828"/>
          <rect x="18" y="2" width="6" height="16" rx="2" fill="#222"/>
          <rect x="50" y="2" width="6" height="16" rx="2" fill="#222"/>
          <path d="M16 38 H58 M16 48 H58 M16 57 H44" stroke="#222" stroke-width="3"/>
        </svg>
      </div>
      You Schedule<br>A Pick-Up
    </div>

    <div class="step step-2">
      <div class="step-circle">
        <svg width="74" height="66" viewBox="0 0 74 66" aria-hidden="true">
          <path d="M37 4 L70 32 H60 V62 H14 V32 H4 Z" fill="#4aa3df" stroke="#1f5f8f" stroke-width="3" stroke-linejoin="round"/>
          <path d="M37 4 L70 32 H4 Z" fill="#e53935"/>
          <rect x="30" y="42" width="14" height="20" fill="#8d5a2b"/>
          <rect x="18" y="38" width="9" height="9" fill="#fff7c2"/>
          <rect x="48" y="38" width="9" height="9" fill="#fff7c2"/>
        </svg>
      </div>
      We Pick-Up<br>Your Dirty Laundry
    </div>

    <div class="step step-3">
      <div class="step-circle">
        <div class="step-art washer" role="img" aria-label="Illustration of washing machines and folded laundry"></div>
      </div>
      We Wash, Dry, Fold<br>&amp; Return Clean Laundry
    </div>

    <div class="step step-4">
      <div class="step-circle">
        <div class="step-art smile" role="img" aria-label="Cartoon of a happy character giving a thumbs up"></div>
      </div>
      Enjoy Effortless<br>Clean Laundry
    </div>
  </section>
</body>
</html>
```